Business Card - connecting 2 souls and beggining the journey of self discovery

Logo on the front
with tag line

On the back list of services and contact details

Seminars
workshops
Coaching
podcasts

Darren Whitlow
Health & Wellbeing Life Coach
0491 372 615
darren@brightcoreliving.example
brightcoreliving.example

Industry/Entity Type

Life Coaching

Contact Information for Business Card

I like the use of colour from the logo to be used. I'm not a fan of white.

Requirements
Must have
• My tagline: Every path inward begins with one step
Nice to have
• Use of colour that is in the mind body soul logo

```html
<!DOCTYPE html>
<html lang="en">
<head>
<meta charset="utf-8">
<title>Brightcore Living – Business Card</title>
<link rel="stylesheet" href="https://fonts.googleapis.com/css2?family=Montserrat:wght@500&family=Source+Sans+3:wght@400;600&display=swap">
<style>
  :root {
    --stage: #c9c9c9;
    --card-grey: #808284;
    --paper: #ffffff;
    --ink-grey: #7d7f81;
    --name-purple: #7b4aa0;
    --icon-orange: #f3a21d;
    --mark-fill: #e9815f;
    --band-green: #6cbf6a;
    --band-purple: #7b4aa0;
    --band-yellow: #f6d03a;
    --band-coral: #ec6f5c;
  }
  * { margin: 0; padding: 0; box-sizing: border-box; }
  html, body {
    width: 1200px; height: 947px; overflow: hidden;
    background: var(--stage);
    font-family: "Source Sans 3", sans-serif;
  }
  .card { position: absolute; left: 263px; width: 674px; overflow: hidden; }
  .card-front { top: 81px; height: 385px; background: var(--card-grey); color: var(--paper); }
  .card-back { top: 482px; height: 386px; background: var(--paper); }

  .brand-mark {
    position: absolute; left: 276px; top: 99px; width: 128px; height: 128px;
    border-radius: 50%; background: var(--mark-fill);
  }
  .brand-name {
    position: absolute; left: 0; right: 0; top: 249px; text-align: center;
    font-family: "Montserrat", sans-serif; font-weight: 500;
    font-size: 38px; letter-spacing: -1.5px; line-height: 44px;
  }
  .tagline {
    position: absolute; left: 0; right: 0; top: 334px; text-align: center;
    font-size: 17px;
  }

  .holder-name {
    position: absolute; left: 0; right: 0; top: 115px; text-align: center;
    color: var(--name-purple); font-weight: 600; font-size: 30px; line-height: 36px;
  }
  .holder-role {
    position: absolute; left: 0; right: 0; top: 151px; text-align: center;
    color: var(--ink-grey); font-size: 17.5px;
  }
  .contact-list {
    position: absolute; left: 0; right: 0; top: 199px; list-style: none;
    color: var(--ink-grey); font-size: 17.5px; line-height: 22px;
  }
  .contact-list li { display: flex; justify-content: center; align-items: center; gap: 4px; }
  .contact-list svg { width: 15px; height: 15px; flex: none; }
  .contact-list .phone { font-weight: 600; }

  .colour-stripe {
    position: absolute; left: 0; right: 0; top: 346px; height: 5px; display: flex;
  }
  .colour-stripe span { flex: 1; }
  .colour-stripe .green { background: var(--band-green); }
  .colour-stripe .purple { background: var(--band-purple); }
  .colour-stripe .yellow { background: var(--band-yellow); }
  .colour-stripe .coral { background: var(--band-coral); }

  .services {
    position: absolute; left: 0; right: 0; top: 353px; height: 33px;
    background: var(--card-grey); color: var(--paper);
    text-align: center; font-size: 17.5px; line-height: 33px;
  }
  .services .dot { margin: 0 7px; font-size: 13px; vertical-align: 1px; }
</style>
</head>
<body>
  <section class="card card-front">
    <div class="brand-mark" aria-hidden="true"></div>
    <h1 class="brand-name">Brightcore Living</h1>
    <p class="tagline">Every path inward begins with one step</p>
  </section>

  <section class="card card-back">
    <h2 class="holder-name">Darren Whitlow</h2>
    <p class="holder-role">Life Coach</p>

    <ul class="contact-list">
      <li class="phone">
        <svg viewBox="0 0 24 24"><path fill="var(--icon-orange)" d="M6.6 10.8a15.2 15.2 0 0 0 6.6 6.6l2.2-2.2a1 1 0 0 1 1-.25 11.4 11.4 0 0 0 3.6.57 1 1 0 0 1 1 1V20a1 1 0 0 1-1 1A17 17 0 0 1 3 4a1 1 0 0 1 1-1h3.5a1 1 0 0 1 1 1c0 1.25.2 2.45.57 3.6a1 1 0 0 1-.25 1z"/></svg>
        0491 372 615
      </li>
      <li class="email">
        <svg viewBox="0 0 24 24"><rect x="2.5" y="5.5" width="19" height="13" rx="1" fill="none" stroke="var(--icon-orange)" stroke-width="2"/><path d="M3 6l9 7 9-7" fill="none" stroke="var(--icon-orange)" stroke-width="2"/></svg>
        darren@brightcoreliving.example
      </li>
      <li class="web">
        <svg viewBox="0 0 24 24" fill="none" stroke="var(--icon-orange)" stroke-width="1.8"><circle cx="12" cy="12" r="9.5"/><ellipse cx="12" cy="12" rx="4" ry="9.5"/><path d="M2.5 12h19M4 7h16M4 17h16"/></svg>
        brightcoreliving.example
      </li>
    </ul>

    <div class="colour-stripe" aria-hidden="true">
      <span class="green"></span><span class="purple"></span><span class="yellow"></span><span class="coral"></span>
    </div>
    <p class="services">Seminars<span class="dot">•</span>Workshops<span class="dot">•</span>Coaching<span class="dot">•</span>Podcasts</p>
  </section>
</body>
</html>
```